Client website

Our designer we were working with had some personal things come up and was unable to finish the design for the site.

We have a .psd file started, and will be attaching it to the project.
Updates

Reason: I still want to polish the designs with the current designer and allow more designers the opportunity to participate.

Reason: I'm extending the deadline for another day to give everyone enough time for the final changes our client wants.

I'm trying to extend the deadline so we can get one last set of comps in for my client.  Could everyone message me and let me know how much time they need to do the final tweaks?

Reason: Hey everyone.  I've been sick the last 3 days and I haven't been able to provide feedback on designs.  I'm extending just a few more days so I can catch up here.  Thanks everyone for your patience.

Target Market(s)

Adults in United States aged 25 to 60 that handle the household budgets and maintenance.

Requirements
Must have
• 1) We need 2 pages. 1 page for flood restoration, 1 page for carpet cleaning

2) The 1-800-# must be the focal point of the website for both pages. People are mostly looking to contact someone ASAP to get them out to their house when flooding occurs.

3) We''re going to have a slide show area to high-light different sub-services offered for each page.

4) We really want a chatterbook / plinker feed area. We''re going to use chatterbook for special offers, and plinker for weather updates. The chatterbook feed is going to be on the carpet cleaning page. The plinker feed is going to be on the flood page.

5) We want an SEO text sections near the bottom.

6) The very bottom will link to the privacy policy and user agreement as well as company name and copyright details.

We really want to stick to the say "theme" that our first designer started with.
Nice to have
• I'm not a designer, so if you think something looks better somewhere, or something can be eliminated, or something can be enhanced, but all means, let us know.

```html
<!DOCTYPE html>
<html lang="en">
<head>
<meta charset="utf-8">
<title>Pura-Fresh Carpet Cleaning</title>
<link href="https://fonts.googleapis.com/css2?family=Open+Sans:wght@400;600;700&family=Arimo:wght@400;700&display=swap" rel="stylesheet">
<style>
:root{
  --page-bg:#1d2935;
  --page-bg-dark:#15202a;
  --blue-bright:#3bb6f0;
  --blue:#2a8fd3;
  --blue-mid:#2f7fc0;
  --blue-deep:#0e5aa6;
  --navy:#103a63;
  --panel:#3478b4;
  --panel-edge:#1f64a6;
  --tab:#2f6fae;
  --tab-edge:#1c5590;
  --green:#28b34a;
  --green-link:#7ef08c;
  --hero-bg:#eef0f1;
  --note:#ece6cf;
  --white:#ffffff;
  --ink-brand:#1582c9;
}
*{box-sizing:border-box;margin:0;padding:0}
html,body{width:1200px;height:1169px;overflow:hidden}
body{background:radial-gradient(ellipse at 50% 30%,#2a3a4a 0%,var(--page-bg) 45%,var(--page-bg-dark) 100%);font-family:Arimo,Arial,sans-serif;color:var(--white);position:relative}
.site{position:absolute;left:134px;top:0;width:935px;height:1169px;background:var(--blue-deep);box-shadow:0 0 30px rgba(0,0,0,.6)}
.callbar{position:absolute;left:0;top:0;width:935px;height:66px;background:linear-gradient(#4cc3f6,#2a98dc);border:2px solid #6fd0f8;border-top:none}
.callbar p{font-family:"Open Sans",sans-serif;font-size:46px;line-height:62px;text-align:center;color:var(--white);letter-spacing:-.5px;text-shadow:0 2px 3px rgba(0,0,0,.35)}
.hero{position:absolute;left:6px;top:68px;width:923px;height:298px;background:linear-gradient(180deg,#f7f8f8,var(--hero-bg))}
.brand{position:absolute;left:22px;top:30px;width:300px;text-align:center}
.brand-mark{width:150px;height:150px;border-radius:50%;background:var(--ink-brand);margin:0 auto 24px}
.brand-name{font-family:"Open Sans",sans-serif;font-weight:700;font-size:42px;line-height:44px;color:var(--ink-brand);letter-spacing:1px}
.brand-tag{font-family:"Open Sans",sans-serif;font-size:15px;color:var(--ink-brand);letter-spacing:2px;margin-top:2px}
.hero-art{position:absolute;left:336px;top:30px;width:587px;height:250px;background:linear-gradient(160deg,#e4e7ea 0%,#6aa1cf 45%,#1d6fb5 100%);opacity:.85;border-radius:4px}
.nav{position:absolute;left:6px;top:366px;width:923px;height:33px;background:linear-gradient(#3fb1ec,#1f86cf);display:flex}
.nav a{width:147px;height:33px;border-right:2px solid #7dcdf5;color:var(--white);text-decoration:none;font-family:"Open Sans",sans-serif;font-size:16px;letter-spacing:1.5px;text-align:center;line-height:36px;border-bottom:2px solid #9ad9f8}
.nav a.active{background:linear-gradient(#4ad35f,var(--green))}
.promo-note{position:absolute;left:765px;top:212px;width:230px;height:215px;background:var(--note);transform:rotate(28deg);box-shadow:4px 6px 10px rgba(0,0,0,.35);border-radius:2px}
.main{position:absolute;left:6px;top:400px;width:923px;height:620px;background:linear-gradient(180deg,#6cc4ee 0%,#3f9bd8 25%,#2c7fc4 60%,#1f69b2 100%)}
.vtab{position:absolute;width:39px;background:var(--tab);border:2px solid var(--tab-edge);box-shadow:0 2px 4px rgba(0,0,0,.25)}
.vtab span{position:absolute;left:50%;top:50%;transform:translate(-50%,-50%) rotate(-90deg);white-space:nowrap;font-family:"Open Sans",sans-serif;font-weight:700;font-size:14px}
.vtab b{position:absolute;bottom:10px;left:0;width:100%;text-align:center;font-family:"Open Sans",sans-serif;font-size:16px}
.tab-1{left:30px;top:36px;height:263px}
.tab-1 span{top:43%}
.tab-1::after{content:"";position:absolute;right:-12px;top:24px;border:11px solid transparent;border-left:11px solid var(--tab);border-right:0}
.tab-2{left:788px;top:36px;height:263px}
.tab-3{left:831px;top:36px;height:263px}
.tab-2 span,.tab-3 span{top:38%}
.intro{position:absolute;left:89px;top:53px;width:390px;font-size:13px;line-height:16.8px}
.intro p+p{margin-top:16px}
.more{position:absolute;left:386px;top:270px;font-family:"Open Sans",sans-serif;font-size:15px;color:var(--green-link);text-decoration:underline}
.photo{position:absolute;left:504px;top:55px;width:254px;height:225px;border-radius:12px;background:linear-gradient(135deg,#f0f2f2,#c9ccce 55%,#8b8f93);box-shadow:0 0 6px rgba(0,0,0,.3)}
.card{position:absolute;top:335px;width:277px;height:214px;background:var(--panel);border:5px solid var(--panel-edge);border-radius:22px;box-shadow:inset 0 0 0 1px #4f93cb}
.card::after{content:"";position:absolute;left:-5px;top:213px;width:277px;height:70px;border-radius:22px 22px 0 0;border:5px solid rgba(31,100,166,.45);border-bottom:none;background:linear-gradient(rgba(52,120,180,.35),rgba(52,120,180,0))}
.card h2{font-family:"Open Sans",sans-serif;font-weight:400;font-size:22px;margin:14px 0 0 15px}
.card-who{left:23px}.card-what{left:313px}.card-find{left:604px}
.card .body{margin:10px 0 0 19px;font-size:13px;line-height:17px;width:225px}
.card .body p+p{margin-top:16px}
.links{list-style:none;margin:9px 0 0 19px}
.links li{font-size:13px;line-height:24px;padding-left:21px;position:relative}
.links li::before{content:"";position:absolute;left:0;top:8px;width:9px;height:9px;background:#5fc0f5}
.links a{color:var(--white)}
.social{display:flex;gap:5px;margin:14px 0 0 17px}
.social a{display:flex;align-items:center;justify-content:center;width:41px;height:36px;border-radius:4px;background:#5aa9e0;color:var(--white);text-decoration:none;font-size:8px;text-align:center;line-height:9px}
.card-find .body{margin-top:12px}
.copy{position:absolute;left:0;top:1020px;width:935px;height:30px;background:linear-gradient(#3aa6ea,#0d56a8);border-top:2px solid #7ccdf6;font-size:11.5px;text-align:center;line-height:34px}
.seo{position:absolute;left:6px;top:1050px;width:923px;height:114px;background:linear-gradient(#0f3258,#123d68);padding:17px 21px;font-size:11px;line-height:14.2px;letter-spacing:-.15px}
</style>
</head>
<body>
<div class="site">
  <header class="callbar"><p>Call Today: 1-800-555-0142</p></header>

  <section class="hero">
    <div class="brand">
      <div class="brand-mark"></div>
      <div class="brand-name">PURA-FRESH</div>
      <div class="brand-tag">CARPET CLEANING</div>
    </div>
    <div class="hero-art" role="img" aria-label="Blue carpet runners unrolling across a bright floor"></div>
  </section>

  <nav class="nav">
    <a class="active" href="#">home</a>
    <a href="#">about</a>
    <a href="#">services</a>
    <a href="#">faq</a>
    <a href="#">contact</a>
  </nav>

  <main class="main">
    <div class="vtab tab-1"><span>We Are Here To Serve You!</span><b>1</b></div>
    <div class="intro">
      <p>Lorem ipsum dolor sit amet, consectetur adipisicing elit, sed do eiusmod tempor incididunt ut labore et dolore magna aliqua. Ut enim ad minim veniam, quis nostrud exercitation ullamco laboris nisi ut aliquip ex ea commodo consequat. Duis aute irure dolor in reprehenderit in voluptate velit esse cillum dolore eu fugiat nulla pariatur. Excepteur sint occaecat cupidatat non proident, sunt in culpa qui officia deserunt mollit anim id est laborum.</p>
      <p>Lorem ipsum dolor sit amet, consectetur adipisicing elit, sed do eiusmod tempor incididunt ut labore et dolore magna aliqua. Ut enim ad minim veniam, quis nostrud exercitation ullamco laboris nisi ut aliquip ex ea commodo consequat.</p>
    </div>
    <a class="more" href="#">View More..</a>
    <div class="photo" role="img" aria-label="Family relaxing at home on a clean white shag carpet"></div>
    <div class="vtab tab-2"><span>About PURA-FRESH</span><b>2</b></div>
    <div class="vtab tab-3"><span>PURA-FRESH Services</span><b>3</b></div>

    <section class="card card-who">
      <h2>Who We Are?</h2>
      <div class="body">
        <p>Lorem ipsum dolor sit amet, consectetur adipisicing elit, sed do eiusmod tempor incididunt ut labore et dolore magna aliqua.</p>
        <p>Ut enim ad minim veniam, quis nostrud exercitation.</p>
      </div>
    </section>
    <section class="card card-what">
      <h2>What We Do?</h2>
      <ul class="links">
        <li><a href="#">Lorem ipsum dolor sit amet,</a></li>
        <li><a href="#">consectetur adipisicing elit</a></li>
        <li><a href="#">sed do eiusmod tempor</a></li>
        <li><a href="#">incididunt ut labore et</a></li>
        <li><a href="#">dolore magna aliqua.</a></li>
      </ul>
    </section>
    <section class="card card-find">
      <h2>Find Us On?</h2>
      <div class="social">
        <a href="#">chatter<br>book</a>
        <a href="#">plinker</a>
        <a href="#">feed</a>
        <a href="#">stashly</a>
      </div>
      <div class="body"><p>Lorem ipsum dolor sit amet, consectetur adipisicing elit, sed do eiusmod tempor incididunt ut labore et dolore magna aliqua.</p></div>
    </section>
  </main>

  <div class="promo-note" role="img" aria-label="Pinned paper note announcing a special promotion"></div>

  <footer>
    <div class="copy">Copyright © 2011 PURA FRESH. All Rights Reserved.</div>
    <div class="seo">Lorem Ipsum is simply dummy text of the printing and typesetting industry. Lorem Ipsum has been the industry's standard dummy text ever since the 1500s, when an unknown printer took a galley of type and scrambled it to make a type specimen book. It has survived not only five centuries, but also the leap into electronic typesetting, remaining essentially unchanged. Lorem Ipsum is simply dummy text of the printing and typesetting industry. Lorem Ipsum has been the industry's standard dummy text ever since the 1500s, when an unknown printer took a galley of type and scrambled it to make a type specimen book. It has survived not only five centuries, but also the leap into electronic typesetting, remaining essentially unchanged.</div>
  </footer>
</div>
</body>
</html>
```